RWT Fittings Ltd Business Cards

We need a business card with our business logo. We provide window and door installations on high-rises in west coast British Colombia, Canada.

I would like my business information and details on one side of the card, and the other side the company name with logo

Target Market(s)

General Contractors

Industry/Entity Type

Construction

Contact Information for Business Card

one side i want my company name and logo in the dark theme logo that i provided

Requirements
Must have
• Marco Peltieri, 16045518293, RWTFittings@mailbox-demo.com, 1407-5194 Linden Row Burnaby BC, V5H 2K9, Owner & Manager

```html
<!DOCTYPE html>
<html lang="en">
<head>
<meta charset="utf-8">
<title>RWT Fittings Ltd – Business Cards</title>
<link href="https://fonts.googleapis.com/css2?family=Open+Sans:wght@400;600;700&display=swap" rel="stylesheet">
<style>
  :root{
    --page:#232323;
    --card:#1f1f24;
    --blue:#29a9e1;
    --white:#f2f2f2;
    --grey:#9a9a9a;
    --rule:#8a8a8a;
    --photo-dark:#1e1c1a;
    --photo-mid:#3b3834;
    --photo-light:#5a5650;
  }
  *{margin:0;padding:0;box-sizing:border-box}
  html,body{width:1200px;height:780px;overflow:hidden;background:var(--page);font-family:"Open Sans",Arial,sans-serif}
  .sheet{position:relative;width:1200px;height:780px}
  .card{position:absolute;top:236px;width:540px;height:309px;overflow:hidden;box-shadow:0 14px 34px rgba(0,0,0,.55)}
  .card--details{left:40px;background:var(--card)}
  .card--brand{left:620px}

  .brand-mark{display:flex;align-items:center;gap:10px}
  .brand-mark__square{width:18px;height:18px;background:var(--blue);flex:none}
  .brand-mark__name{color:var(--blue);font-weight:700;white-space:nowrap}

  /* contact side */
  .card--details .brand-mark{position:absolute;left:34px;top:46px}
  .card--details .brand-mark__name{font-size:24px}
  .divider{position:absolute;left:0;top:0}
  .person{position:absolute;left:290px;top:100px;width:240px}
  .person__name{color:var(--blue);font-size:26px;font-weight:700;line-height:1.1;white-space:nowrap}
  .person__title{color:var(--white);font-size:13px;margin-top:4px}
  .contacts{list-style:none;margin-top:14px}
  .contacts li{display:flex;align-items:center;gap:8px;color:var(--white);font-size:13px;line-height:1.75;white-space:nowrap}
  .contacts svg{width:13px;height:13px;flex:none}
  .address-band{position:absolute;left:0;bottom:26px;width:420px;height:36px;background:var(--blue);color:var(--white);font-size:13px;display:flex;align-items:center;padding-left:28px;white-space:nowrap}
  .corner-block{position:absolute;right:30px;bottom:0;width:70px;height:56px;background:var(--grey)}

  /* brand side */
  .backdrop{position:absolute;inset:0;background:
    radial-gradient(ellipse at 75% 70%,var(--photo-light) 0%,transparent 60%),
    linear-gradient(135deg,var(--photo-dark) 0%,var(--photo-mid) 60%,var(--photo-light) 100%)}
  .card--brand .brand-mark{position:absolute;left:50%;top:50%;transform:translate(-50%,-50%);gap:14px}
  .card--brand .brand-mark__square{width:26px;height:26px}
  .card--brand .brand-mark__name{font-size:36px}
</style>
</head>
<body>
<main class="sheet">
  <section class="card card--details" aria-label="Business card, contact side">
    <div class="brand-mark">
      <span class="brand-mark__square"></span>
      <span class="brand-mark__name">RWT Fittings Ltd</span>
    </div>
    <svg class="divider" width="540" height="309" aria-hidden="true">
      <line x1="290" y1="80" x2="180" y2="210" stroke="var(--rule)" stroke-width="1"/>
    </svg>
    <div class="person">
      <p class="person__name">Marco Peltieri</p>
      <p class="person__title">Owner &amp; Manager</p>
      <ul class="contacts">
        <li><svg viewBox="0 0 24 24"><path fill="#29a9e1" d="M6.6 10.8a15 15 0 0 0 6.6 6.6l2.2-2.2a1 1 0 0 1 1-.25 11.4 11.4 0 0 0 3.6.57 1 1 0 0 1 1 1V20a1 1 0 0 1-1 1A17 17 0 0 1 3 4a1 1 0 0 1 1-1h3.5a1 1 0 0 1 1 1c0 1.25.2 2.45.57 3.57a1 1 0 0 1-.25 1z"/></svg>16045518293</li>
        <li><svg viewBox="0 0 24 24"><rect x="2" y="5" width="20" height="14" rx="2" fill="#29a9e1"/><path d="M3 6l9 7 9-7" stroke="#1f1f24" stroke-width="2" fill="none"/></svg>RWTFittings@mailbox-demo.com</li>
        <li><svg viewBox="0 0 24 24"><circle cx="12" cy="12" r="10" fill="#29a9e1"/><path d="M2 12h20M12 2c3 3 3 17 0 20M12 2c-3 3-3 17 0 20" stroke="#1f1f24" stroke-width="1.6" fill="none"/></svg>www.rwtfittings-demo.com</li>
      </ul>
    </div>
    <p class="address-band">1407-5194 Linden Row Burnaby BC, V5H 2K9</p>
    <span class="corner-block"></span>
  </section>

  <section class="card card--brand" aria-label="Business card, brand side">
    <div class="backdrop" role="img" aria-label="Dim, softly blurred office interior photograph with a potted plant"></div>
    <div class="brand-mark">
      <span class="brand-mark__square"></span>
      <span class="brand-mark__name">RWT Fittings Ltd</span>
    </div>
  </section>
</main>
</body>
</html>
```